Harbourline Electrical Solutions

On one side. LOGO (underneath:) Commercial Industrial Residential

- NAME & CONTACT DETAILS

Marcus T. Hollings
Project Manager

(Cell icon) (441) 555-0187
(Email icon) hlelectricalsolutions@mailvento.com
(Facebook & Instagram icons )@hlelectricalsolutions

Other side: LOGO - underneath ELECTRICAL CONSTRUCTION & MAINTENANCE . LED LIGHTING & AUTOMATION . LIFE SAFETY SYSTEMS (FIRE ALARM / SECURITY) . DATA & COMMUNICATION

```html
<!DOCTYPE html>
<html lang="en">
<head>
<meta charset="utf-8">
<title>Harbourline Electrical Solutions – Business Card</title>
<link rel="stylesheet" href="https://fonts.googleapis.com/css2?family=Montserrat:wght@500;600&family=Roboto:wght@400;500&family=Roboto+Condensed:ital,wght@1,500&display=swap">
<style>
  :root {
    --backdrop: #3b3b3d;
    --card: #1c1c1e;
    --card-edge: #141415;
    --ink: #f2f2f2;
    --muted: #8c8c90;
    --accent: #1e88d0;
    --band: #0c5a77;
    --name-blue: #13678a;
  }
  * { margin: 0; padding: 0; box-sizing: border-box; }
  html, body { width: 799px; height: 1200px; overflow: hidden; }
  body {
    background: var(--backdrop);
    font-family: "Roboto", Arial, sans-serif;
    color: var(--ink);
    position: relative;
  }
  .card {
    position: absolute;
    left: 90px;
    width: 620px;
    height: 354px;
    background: var(--card);
    border: 1px solid var(--card-edge);
    box-shadow: 0 10px 30px rgba(0,0,0,.45);
    overflow: hidden;
  }
  .card--front { top: 120px; }
  .card--back  { top: 700px; }

  /* Front */
  .front-brand {
    position: absolute;
    right: 40px;
    top: 48px;
    display: flex;
    align-items: center;
    gap: 14px;
  }
  .front-brand__mark {
    width: 14px; height: 14px;
    background: var(--muted);
  }
  .front-brand__name {
    font-family: "Montserrat", sans-serif;
    font-weight: 500;
    font-size: 20px;
    letter-spacing: 4px;
    line-height: 1.25;
    text-transform: uppercase;
    color: var(--muted);
  }
  .services {
    position: absolute;
    left: 40px;
    top: 168px;
    right: 40px;
    font-size: 14.5px;
    line-height: 1.45;
    color: var(--ink);
  }
  .rule {
    position: absolute;
    left: 40px; right: 40px;
    top: 222px;
    height: 2px;
    background: var(--accent);
  }
  .sectors {
    position: absolute;
    left: 40px;
    top: 250px;
    font-family: "Montserrat", sans-serif;
    font-weight: 600;
    font-size: 15px;
    letter-spacing: 2.5px;
    color: var(--ink);
  }
  .sectors span.sep { margin: 0 14px; }

  /* Back */
  .back-brand {
    position: absolute;
    left: 36px;
    top: 90px;
    width: 230px;
    font-family: "Montserrat", sans-serif;
    font-weight: 600;
    font-size: 24px;
    line-height: 1.2;
    letter-spacing: 1.5px;
    text-transform: uppercase;
    color: var(--ink);
  }
  .back-brand__mark {
    display: block;
    width: 16px; height: 16px;
    border-radius: 50%;
    background: var(--ink);
    margin-bottom: 12px;
  }
  .contact {
    position: absolute;
    left: 300px;
    top: 74px;
  }
  .contact__name {
    font-family: "Roboto Condensed", sans-serif;
    font-style: italic;
    font-weight: 500;
    font-size: 25px;
    color: var(--name-blue);
  }
  .contact__role {
    font-size: 15px;
    color: var(--ink);
    margin-bottom: 12px;
  }
  .contact__list { list-style: none; }
  .contact__list li {
    display: flex;
    align-items: center;
    gap: 10px;
    font-size: 15px;
    line-height: 1.55;
  }
  .icon { width: 13px; height: 13px; flex: none; }
  .icon--dot { border-radius: 50%; background: var(--muted); }
  .band {
    position: absolute;
    left: 0; right: 0; bottom: 0;
    height: 62px;
    background: var(--band);
    display: flex;
    align-items: center;
    padding-left: 36px;
    font-family: "Montserrat", sans-serif;
    font-weight: 500;
    font-size: 14px;
    letter-spacing: 2px;
  }
  .band span.sep { margin: 0 14px; }
</style>
</head>
<body>

<section class="card card--front" aria-label="Business card front">
  <div class="front-brand">
    <span class="front-brand__mark"></span>
    <div class="front-brand__name">Harbourline<br>Electrical<br>Solutions</div>
  </div>
  <p class="services">
    Electrical Construction &amp; Maintenance | Led Lighting &amp; Automation<br>
    Life Safety Systems (Fire Alarm/Security) | Data &amp; Communication
  </p>
  <div class="rule"></div>
  <div class="sectors">COMMERCIAL<span class="sep">|</span>INDUSTRIAL<span class="sep">|</span>RESIDENTIAL</div>
</section>

<section class="card card--back" aria-label="Business card back">
  <div class="back-brand">
    <span class="back-brand__mark"></span>
    Harbourline<br>Electrical<br>Solutions
  </div>
  <div class="contact">
    <div class="contact__name">Marcus T. Hollings</div>
    <div class="contact__role">Project Manager</div>
    <ul class="contact__list">
      <li>
        <svg class="icon" viewBox="0 0 16 16" aria-hidden="true"><path fill="#8c8c90" d="M3 1h3l1.5 4-2 1.3a9 9 0 0 0 4.2 4.2L11 8.5l4 1.5v3a2 2 0 0 1-2 2A12 12 0 0 1 1 3a2 2 0 0 1 2-2z"/></svg>
        (441) 555-0187
      </li>
      <li>
        <svg class="icon" viewBox="0 0 16 16" aria-hidden="true"><rect x="1" y="3" width="14" height="10" rx="1" fill="#8c8c90"/><path d="M1.5 4l6.5 5 6.5-5" stroke="#1c1c1e" stroke-width="1.4" fill="none"/></svg>
        hlelectricalsolutions@mailvento.com
      </li>
      <li><span class="icon icon--dot"></span>@hlelectricalsolutions</li>
      <li><span class="icon icon--dot"></span>@hlelectricalsolutions</li>
    </ul>
  </div>
  <div class="band">COMMERCIAL<span class="sep">|</span>INDUSTRIAL<span class="sep">|</span>RESIDENTIAL</div>
</section>

</body>
</html>
```